Retail Sign for Houseplant Campaign

Sign will measure 3 to 4 foot tall by 22.2inches and place on rolling racks of houseplants for a retail promotion in The Birchwell Yard. The theme of the promotion will be "New Year, New You!" Selling points which should be on the sign are Houseplants give you a taste of nature, Houseplants boost air quality inside your home, Indoor plants reduce anxiety, Indoor plants make you more productive, Houseplants improve your concentration and memory.
Updates

Target Market(s)

People who love plants

Industry/Entity Type

Horticulture/ retail

Colors
00AB8E
00BBA5
67D7C9
C6EFE9
E9F9F6
59FF00
82FF00
B8FF75
E3FFCB
F4FFEA
FFF300
FFF600
FEFA6F
FFFEC7
FFFEE8

Requirements
Must have
• Must feel energetic and encourage people to buy plants. Should include 1-2 photos and the selling points listed

```html
<!DOCTYPE html>
<html lang="en">
<head>
<meta charset="utf-8">
<title>New Year New You – The Birchwell Yard Houseplant Sign</title>
<link rel="stylesheet" href="https://fonts.googleapis.com/css2?family=Chewy&family=Roboto+Condensed:wght@700&family=Montserrat:wght@400&display=swap">
<style>
  :root {
    --stage: #eef3f1;
    --mist-light: #e9f5f2;
    --mist-mid: #c6e6df;
    --mist-teal: #5fb7a3;
    --brand-teal: #1f9a80;
    --title-teal: #0f8a6c;
    --bullet-teal: #2a8a74;
    --photo-dark: #27413d;
    --photo-mid: #5e7f7a;
    --white: #ffffff;
  }
  * { margin: 0; padding: 0; box-sizing: border-box; }
  html, body {
    width: 961px; height: 1200px; overflow: hidden;
    background: var(--stage);
  }
  .sign {
    position: absolute; left: 110px; top: 0;
    width: 741px; height: 1200px; overflow: hidden;
    background:
      radial-gradient(ellipse 60% 35% at 85% 12%, rgba(255,255,255,.85), transparent 70%),
      radial-gradient(ellipse 70% 30% at 50% 55%, rgba(233,245,242,.9), transparent 75%),
      radial-gradient(ellipse 45% 30% at 10% 25%, var(--mist-teal), transparent 80%),
      linear-gradient(180deg, #9fd8ca 0%, var(--mist-mid) 30%, #dde9e6 55%, #b9d9d1 70%, var(--mist-light) 100%);
  }
  .brand {
    position: absolute; left: 32px; top: 30px;
    display: flex; align-items: center; gap: 10px;
    font-family: "Montserrat", sans-serif; font-weight: 400;
    font-size: 30px; color: var(--brand-teal); letter-spacing: .5px;
  }
  .brand-mark { width: 40px; height: 40px; background: var(--brand-teal); }
  .brush {
    position: absolute; left: 59px; top: 160px; width: 593px; height: 190px;
    border-radius: 40px 90px 60px 30px / 50px 70px 60px 80px;
    background: linear-gradient(90deg, rgba(31,154,128,.55), #3aa98f 40%, #33a68c 80%, rgba(31,154,128,.6));
  }
  .headline {
    position: absolute; left: 0; width: 100%; top: 150px;
    font-family: "Chewy", cursive; color: var(--title-teal);
    -webkit-text-stroke: 0; text-align: center;
    text-shadow:
      0 0 0 var(--white),
      3px 0 var(--white), -3px 0 var(--white), 0 3px var(--white), 0 -3px var(--white),
      2px 2px var(--white), -2px 2px var(--white), 2px -2px var(--white), -2px -2px var(--white),
      4px 5px 6px rgba(0,0,0,.25);
  }
  .headline .line-one { display: block; font-size: 70px; line-height: 1; margin-left: 150px; }
  .headline .line-two { display: block; font-size: 110px; line-height: 1; margin-left: 40px; }
  .selling-points {
    position: absolute; left: 90px; top: 402px; list-style: none;
    font-family: "Roboto Condensed", sans-serif; font-weight: 700;
    font-size: 22px; color: var(--bullet-teal); letter-spacing: -.2px;
  }
  .selling-points li {
    display: flex; align-items: center; gap: 10px; height: 43px;
  }
  .selling-points li::before {
    content: ""; width: 10px; height: 10px; border-radius: 50%;
    background: var(--bullet-teal); flex: none;
  }
  .photo {
    position: absolute; left: 0; bottom: 0; width: 100%; height: 520px;
    background:
      radial-gradient(ellipse 30% 45% at 85% 55%, #1f3d36, transparent 75%),
      radial-gradient(ellipse 30% 50% at 30% 70%, #e8ecea, transparent 70%),
      linear-gradient(180deg, rgba(185,217,209,0) 0%, var(--photo-mid) 25%, var(--photo-dark) 100%);
  }
</style>
</head>
<body>
  <main class="sign">
    <div class="brand"><span class="brand-mark"></span><span class="brand-name">VERDANT LOFT</span></div>

    <div class="brush" role="img" aria-label="Teal painted brush stroke behind the headline"></div>
    <h1 class="headline">
      <span class="line-one">New Year</span>
      <span class="line-two">New You!</span>
    </h1>

    <ul class="selling-points">
      <li>HOUSEPLANTS GIVE YOU A TASTE OF NATURE</li>
      <li>HOUSEPLANTS BOOST AIR QUALITY INSIDE YOUR HOME</li>
      <li>INDOOR PLANTS REDUCE ANXIETY</li>
      <li>INDOOR PLANTS MAKE YOU MORE PRODUCTIVE</li>
      <li>HOUSEPLANTS IMPROVE YOUR CONCENTRATION AND MEMORY</li>
    </ul>

    <div class="photo" role="img" aria-label="Photo of a smiling woman in a white top wiping the leaves of a large monstera houseplant indoors"></div>
  </main>
</body>
</html>
```